Business Intelligence Application - Reporting Menu and Report Criteria Design

Looking for a fresh, effective and user friendly view for the menu structure and reporting criteria screen format for a business reporting application. Initial format completed, content structure is in place, but we need the 'wow' design.. as its a serious professional report/BI tool it has to fall within certain guidelines for clarity and graphics..but we want it to be slick, friendly, great user experience. There is a large amount of complex content to fit into a small space and we need it to be very inviting, modern and intuitive.. If interested, please review the attachment. We have live screens in operation, but feel these could be improved and looking forward to seeing what great creative suggestions could be made. Please review work done to date in the attached.. We are not looking for a total re-design of everything, all the basic business content/structure is there.. but tell us what we could do to improve this in terms of graphic design... particularly the criteria screens.. thanks!
Updates

Reason: Need a few more days to review designs - thanks for all submissions so far, we will make a selection shortly.

Target Market(s)

Business analysts, hotel operations teams, finance analysts hospitality industry

Industry/Entity Type

Hospitality

Coding

Coded - Design and coding required

Number of Pages Required

4 page

Font styles to use
Sans Serif
Other font styles liked:
• Candara, please see example in deck

Colors
3276b5
3176b5
0255a3
85acd3
33a6d7
cee9f5
85cae6

Requirements
Must have
• sharp clear, logical menu structure, (currently it has 'clicks to sub-menus, we need hover over, slide to sub-menus..) colour, styling.. and most focus on revision of criteria.. right now is somewhat heavy, cumbersome.. keep colour and friendly intuitive process steps.. its heavy analytical stuff.. best of luck!
Should not have
• No grey fonts on white or grey screens! many business apps are not readable or sharp.. or fonts are too small.. colourless, so please avoid that.. see our deck - sharp dark (navy) or black fonts on white, or light shading..

```html
<!DOCTYPE html>
<html lang="en">
<head>
<meta charset="utf-8">
<title>Yieldcast – Property Search</title>
<link rel="stylesheet" href="https://fonts.googleapis.com/css2?family=Lato:wght@400;700&family=Open+Sans:wght@400&display=swap">
<style>
  :root{
    --navy-deep:#011638;
    --nav-blue:#0a55a3;
    --brand-blue:#0556a6;
    --sky:#4fb3e0;
    --panel:#52b2de;
    --bg-top:#2f9cd5;
    --bg-bottom:#0b5aa8;
    --icon-blue:#1f7fc8;
    --cyan:#3ad8e6;
    --white:#ffffff;
    --field-top:#ffffff;
    --field-bottom:#ececec;
    --text-navy:#0a4f9c;
    --footer:#e0e0e0;
    --ink:#111111;
  }
  *{box-sizing:border-box;margin:0;padding:0}
  html,body{width:1200px;height:664px;overflow:hidden}
  body{font-family:"Lato",sans-serif;position:relative;background:var(--bg-bottom)}

  .app-header{position:absolute;left:0;top:0;width:1200px;height:113px;background:var(--navy-deep)}
  .brand{position:absolute;left:97px;top:38px;display:flex;align-items:center;gap:14px}
  .brand-mark{width:34px;height:34px;border-radius:50%;background:var(--cyan)}
  .brand-name{font-size:28px;font-weight:700;color:var(--white)}
  .user{position:absolute;left:781px;top:34px;display:flex;align-items:center;gap:8px}
  .user-avatar{width:44px;height:44px;border-radius:50%;background:linear-gradient(#c9b7a4,#6c5b4f)}
  .user-greeting{color:var(--white);font-size:15px;line-height:21px}
  .user-greeting strong{font-weight:700;display:block}
  .header-divider{position:absolute;top:40px;width:1px;height:38px;background:#1e3358}
  .header-icon{position:absolute;top:42px}

  .main-nav{position:absolute;left:0;top:113px;width:1200px;height:51px;background:var(--nav-blue)}
  .nav-item{position:absolute;top:0;height:51px;display:flex;align-items:center;justify-content:center;
    font-size:13px;font-weight:700;color:var(--white);border-right:1px solid #3d7dbf}
  .nav-item.is-open{background:var(--white);color:var(--brand-blue);border-right:none}
  .nav-item.is-active{background:var(--sky)}
  .nav-item.is-active .nav-badge{width:20px;height:20px;border-radius:50%;background:#b07a3e;margin-right:5px}

  .stage{position:absolute;left:0;top:164px;width:1200px;height:424px;background:linear-gradient(var(--bg-top),var(--bg-bottom))}
  .criteria-panel{position:absolute;left:112px;top:19px;width:974px;height:320px;background:var(--panel)}
  .field-label{position:absolute;color:var(--white);font-size:17.5px;font-weight:700;letter-spacing:.2px}
  .field-label.is-plain{font-weight:400}
  .field{position:absolute;height:43px;background:linear-gradient(var(--field-top),var(--field-bottom));
    border:1px solid #c9d9e6;color:var(--text-navy);font-size:16.5px;display:flex;align-items:center;padding-left:18px}
  .search-button{position:absolute;left:708px;top:233px;width:215px;height:51px;background:var(--brand-blue);
    color:var(--white);font-size:21px;font-weight:700;display:flex;align-items:center;justify-content:center;border:none}

  .dropdown{position:absolute;left:72px;top:164px;width:265px;height:173px;background:var(--white);box-shadow:0 2px 6px rgba(0,0,0,.25)}
  .dropdown-item{position:absolute;left:0;width:265px;height:37px;display:flex;align-items:center;padding-left:33px;
    color:var(--brand-blue);font-size:16px}
  .dropdown-item.is-active{background:var(--brand-blue);color:var(--white)}
  .dropdown-item svg{position:absolute;right:12px;top:11px}
  .submenu{position:absolute;left:337px;top:244px;width:212px;height:260px;background:var(--white);box-shadow:0 2px 6px rgba(0,0,0,.25)}
  .submenu-item{position:absolute;left:33px;color:var(--brand-blue);font-size:14px}

  .app-footer{position:absolute;left:0;top:588px;width:1200px;height:76px;background:var(--footer);
    display:flex;align-items:center;justify-content:center;font-family:"Open Sans",sans-serif;font-size:14px;color:var(--ink)}
</style>
</head>
<body>
  <header class="app-header">
    <div class="brand"><span class="brand-mark"></span><span class="brand-name">Yieldcast</span></div>
    <div class="user">
      <div class="user-avatar" role="img" aria-label="User profile photo"></div>
      <div class="user-greeting">Welcome<strong>Admin</strong></div>
    </div>
    <span class="header-divider" style="left:919px"></span>
    <svg class="header-icon" style="left:946px" width="28" height="30" viewBox="0 0 28 30" aria-label="Notifications">
      <path d="M14 2c-5 0-8 4-8 9v7l-3 4h22l-3-4v-7c0-5-3-9-8-9z" fill="var(--icon-blue)"/>
      <circle cx="14" cy="25" r="3" fill="var(--icon-blue)"/>
    </svg>
    <span class="header-divider" style="left:1005px"></span>
    <svg class="header-icon" style="left:1034px" width="30" height="26" viewBox="0 0 30 26" aria-label="Log out">
      <path d="M18 1l11 9-11 9v-5C10 14 5 17 2 24c0-9 5-15 16-16z" fill="var(--icon-blue)"/>
    </svg>
  </header>

  <nav class="main-nav">
    <div class="nav-item is-open" style="left:73px;width:69px">Admin</div>
    <div class="nav-item" style="left:142px;width:96px">Management</div>
    <div class="nav-item" style="left:238px;width:144px">Rooms Performance</div>
    <div class="nav-item" style="left:382px;width:133px">Revenue Summary</div>
    <div class="nav-item" style="left:515px;width:112px">Demand &amp; Risk</div>
    <div class="nav-item" style="left:627px;width:132px">Inventory Analysis</div>
    <div class="nav-item" style="left:759px;width:89px">Placeholder</div>
    <div class="nav-item is-active" style="left:848px;width:141px"><span class="nav-badge" role="img" aria-label="Section mascot icon"></span>Property Search</div>
    <div class="nav-item" style="left:989px;width:43px">Intel</div>
    <div class="nav-item" style="left:1032px;width:70px;border-right:none">Planning</div>
  </nav>

  <main class="stage">
    <section class="criteria-panel">
      <div class="field-label" style="left:48px;top:56px">SEARCH NAME</div>
      <div class="field" style="left:45px;top:74px;width:287px"></div>
      <div class="field-label" style="left:348px;top:56px">SEARCH ID</div>
      <div class="field" style="left:339px;top:74px;width:287px"></div>
      <div class="field-label" style="left:641px;top:56px">SEARCH PRODUCT</div>
      <div class="field" style="left:639px;top:74px;width:283px"></div>

      <div class="field-label" style="left:46px;top:157px">DIVISIONS</div>
      <div class="field" style="left:45px;top:175px;width:287px">Europe</div>
      <div class="field-label is-plain" style="left:348px;top:157px">Countries</div>
      <div class="field" style="left:339px;top:175px;width:287px">England</div>
      <div class="field-label is-plain" style="left:640px;top:157px">Areas</div>
      <div class="field" style="left:639px;top:175px;width:283px">Central London</div>

      <button class="search-button">SEARCH</button>
    </section>
  </main>

  <div class="dropdown">
    <div class="dropdown-item" style="top:8px">Registration</div>
    <div class="dropdown-item" style="top:45px">User Access</div>
    <div class="dropdown-item is-active" style="top:81px">Setup
      <svg width="10" height="16" viewBox="0 0 10 16"><path d="M2 1l7 7-7 7" fill="none" stroke="#ffffff" stroke-width="1.5"/></svg>
    </div>
    <div class="dropdown-item" style="top:119px">Data Imports</div>
  </div>

  <div class="submenu">
    <div class="submenu-item" style="top:24px">Market Segments</div>
    <div class="submenu-item" style="top:52px">Banquet &amp; Catering</div>
    <div class="submenu-item" style="top:80px">Outlets/F&amp;B Service</div>
    <div class="submenu-item" style="top:108px">Other Income</div>
    <div class="submenu-item" style="top:137px">Impact Dates</div>
    <div class="submenu-item" style="top:165px">Inventory</div>
    <div class="submenu-item" style="top:193px">Geo/Location</div>
    <div class="submenu-item" style="top:221px">Distribution Channels</div>
  </div>

  <footer class="app-footer">© 2017 Company Name&nbsp; All right reserved&nbsp; Term of Use</footer>
</body>
</html>
```